Lunelle Rosa Hair Fancy Business Card’s

I want my business cards to be elite, original and very classy. I want the business cards to match the colors of my logo and to match the design posted. I would love the design of the picture I posted

I want the card all white .
The dripping on the top of the card I want it to match the pink color in my logo that’s also posted .
I need my logo on the business card !
I need my Instagram- @lunelle.rosa.hair__
And my phone number - 555 207 3962

Target Market(s)

My target market is young woman age 23 to older woman to the age of 65
I want both older and younger women to love my design . I don’t want any cheap looking business cards

Industry/Entity Type

Hair And Beauty

Contact Information for Business Card

Add my logo
Add my Instagram- @lunelle.rosa.hair__
My number - 555 207 3962
My website- www.lunellerosahair.example

Font styles to use
Serif
Script

Colors
ffffff
e667a6
e34298

Requirements
Must have
• The business cards must have my logo, my number , my website, and my Instagram!
Nice to have
• Nice to have glitter words that match my logo
• The business cards must look classy and mature
• I want them to be very unique!!
Should not have
• Should not have any colors that doesn’t match my logo ! This is very important! Please

```html
<!DOCTYPE html>
<html lang="en">
<head>
<meta charset="utf-8">
<title>Lunelle Rosa Hair – Business Cards</title>
<link href="https://fonts.googleapis.com/css2?family=Roboto:wght@300&display=swap" rel="stylesheet">
<style>
  :root {
    --white: #ffffff;
    --pink-light: #e667a6;
    --pink-deep: #e34298;
    --ink-grey: #8a8a8c;
    --backdrop: #ececee;
  }
  * { box-sizing: border-box; margin: 0; padding: 0; }
  html, body {
    width: 1200px; height: 1200px; overflow: hidden;
    background: var(--backdrop);
    font-family: "Roboto", Arial, sans-serif;
    font-weight: 300;
  }
  .card {
    position: absolute;
    left: 225px;
    width: 750px; height: 450px;
    background: var(--white);
    overflow: hidden;
  }
  .card--front { top: 112px; }
  .card--back { top: 637px; }
  .card__waves { position: absolute; inset: 0; width: 750px; height: 450px; }
  .wave--light { fill: var(--pink-light); }
  .wave--deep { fill: var(--pink-deep); }
  .brand-name {
    position: absolute; left: 0; right: 0;
    text-align: center;
    color: var(--pink-deep);
    font-size: 44px;
    letter-spacing: 1px;
  }
  .card--front .brand-name { top: 180px; }
  .card--back .brand-name { top: 64px; }
  .divider-glow {
    position: absolute; left: 247px; top: 218px;
    width: 248px; height: 26px;
    background: radial-gradient(ellipse at 50% 20%, rgba(0,0,0,0.13), rgba(0,0,0,0) 70%);
  }
  .contact-list {
    position: absolute; left: 224px; top: 283px;
    list-style: none;
  }
  .contact-item {
    display: flex; align-items: center;
    height: 37px;
    color: var(--ink-grey);
    font-size: 25px;
  }
  .contact-icon { width: 29px; height: 29px; margin-right: 24px; flex: none; }
  .contact-icon * { fill: none; stroke: var(--pink-deep); stroke-width: 2.6; stroke-linecap: round; stroke-linejoin: round; }
</style>
</head>
<body>
  <section class="card card--front">
    <svg class="card__waves" viewBox="0 0 750 450" aria-hidden="true">
      <path class="wave--light" d="M0,0 H89 Q40,8 0,42 Z"/>
      <path class="wave--deep" d="M0,0 H62 Q25,8 0,30 Z"/>
      <path class="wave--light" d="M750,304 Q620,415 418,450 L750,450 Z"/>
      <path class="wave--deep" d="M750,346 Q640,425 471,450 L750,450 Z"/>
    </svg>
    <p class="brand-name">Lunelle Rosa Hair</p>
  </section>

  <section class="card card--back">
    <svg class="card__waves" viewBox="0 0 750 450" aria-hidden="true">
      <path class="wave--light" d="M0,0 H334 Q140,35 0,147 Z"/>
      <path class="wave--deep" d="M0,0 H281 Q110,25 0,105 Z"/>
      <path class="wave--light" d="M750,408 Q710,440 662,450 L750,450 Z"/>
      <path class="wave--deep" d="M750,428 Q722,445 688,450 L750,450 Z"/>
    </svg>
    <p class="brand-name">Lunelle Rosa Hair</p>
    <div class="divider-glow"></div>
    <ul class="contact-list">
      <li class="contact-item">
        <svg class="contact-icon" viewBox="0 0 30 30" aria-hidden="true">
          <path d="M6 3 L11 3 L13 9 L10 12 Q13 18 18 20 L21 17 L27 19 L27 24 Q26 27 22 27 Q4 24 3 7 Q3 3 6 3 Z"/>
        </svg>
        <span>555 207 3962</span>
      </li>
      <li class="contact-item">
        <svg class="contact-icon" viewBox="0 0 30 30" aria-hidden="true">
          <rect x="3" y="3" width="24" height="24" rx="5"/>
        </svg>
        <span>@lunelle.rosa.hair__</span>
      </li>
      <li class="contact-item">
        <svg class="contact-icon" viewBox="0 0 30 30" aria-hidden="true">
          <circle cx="15" cy="15" r="12"/>
          <ellipse cx="15" cy="15" rx="5" ry="12"/>
          <path d="M3 15 H27"/>
        </svg>
        <span>www.lunellerosahair.example</span>
      </li>
    </ul>
  </section>
</body>
</html>
```